Mosquito and outdoor pest management

The uploaded logo must be integrated as the main theme of the card. I would like it to be modern and eye catching. Maybe some backround images or light silver metallic background.
Space enough at the base for contact info to be put in- phone numbers,emails,names,website.
Space on the back for short blog and lines for hand writing..calling card.
Commercial- golf courses, schools, outdoor function properties, pre event treatments.
Residential- retirement villages, townhome complexes and general houses
Management

```html
<!DOCTYPE html>
<html lang="en">
<head>
<meta charset="utf-8">
<title>Larkfield Yard Care – Business Card</title>
<link href="https://fonts.googleapis.com/css2?family=Libre+Baskerville:wght@400;700&display=swap" rel="stylesheet">
<style>
  :root {
    --backdrop: #2a2a2c;
    --card-white: #ffffff;
    --steel-light: #d9d9dc;
    --steel-mid: #a9a9ad;
    --steel-dark: #7d7d82;
    --ink: #141414;
    --brand-red: #e3222b;
    --text-light: #ffffff;
  }
  * { box-sizing: border-box; margin: 0; padding: 0; }
  html, body { width: 1200px; height: 900px; overflow: hidden; }
  body {
    background: var(--backdrop);
    font-family: "Libre Baskerville", Georgia, serif;
    position: relative;
  }
  .card {
    position: absolute;
    left: 250px;
    width: 700px;
    height: 400px;
    box-shadow: 0 10px 30px rgba(0,0,0,.45);
    overflow: hidden;
  }
  .card--front { top: 30px; background: var(--card-white); }
  .card--back {
    top: 470px;
    background: linear-gradient(160deg, var(--steel-light) 0%, var(--steel-mid) 55%, var(--steel-dark) 100%);
  }

  .brand {
    position: absolute;
    display: flex;
    align-items: center;
    gap: 14px;
    color: var(--ink);
    font-family: "Libre Baskerville", Georgia, serif;
    font-weight: 700;
    white-space: nowrap;
  }
  .brand__dot {
    width: 20px; height: 20px; border-radius: 50%;
    background: var(--brand-red); flex: none;
  }
  .brand__name { font-size: 40px; line-height: 1; }

  .card--front .brand { left: 160px; top: 220px; }
  .card--back .brand { left: 50px; top: 70px; }
  .card--back .brand__name { font-size: 34px; }

  .steel-band {
    position: absolute;
    left: 300px; top: 236px;
    width: 400px; height: 164px;
    background: linear-gradient(90deg, #8e8e93 0%, #c9c9cc 30%, #f4f4f5 55%, #6f6f74 78%, #b8b8bc 100%);
  }
  .red-rule {
    position: absolute;
    left: 250px; top: 232px;
    width: 450px; height: 3px;
    background: var(--brand-red);
  }
  .screw { position: absolute; width: 20px; height: 20px; }
  .screw--left { left: 322px; top: 262px; }
  .screw--right { left: 660px; top: 262px; }

  .person {
    position: absolute;
    left: 38px; top: 200px;
    padding-left: 18px;
    border-left: 10px solid var(--brand-red);
  }
  .person__name {
    font-weight: 700; font-size: 24px; letter-spacing: 1px;
    color: var(--text-light); text-transform: uppercase; line-height: 1.1;
  }
  .person__role {
    font-size: 12px; font-weight: 700; letter-spacing: 1px;
    color: var(--ink); text-transform: uppercase; margin-top: 4px;
  }
  .contacts {
    position: absolute;
    left: 48px; top: 286px;
    list-style: none;
    color: var(--text-light);
    font-size: 15px;
  }
  .contacts li { display: flex; align-items: center; gap: 12px; margin-bottom: 8px; }
  .contacts svg { width: 14px; height: 14px; fill: var(--ink); flex: none; }
</style>
</head>
<body>

<section class="card card--front">
  <div class="brand">
    <span class="brand__dot"></span>
    <span class="brand__name">Larkfield Yard Care</span>
  </div>
</section>

<section class="card card--back">
  <div class="brand">
    <span class="brand__dot"></span>
    <span class="brand__name">Larkfield Yard Care</span>
  </div>

  <div class="steel-band"></div>
  <div class="red-rule"></div>
  <svg class="screw screw--left" viewBox="0 0 20 20" aria-hidden="true">
    <circle cx="10" cy="10" r="9" fill="#3a3a3d"/><circle cx="10" cy="10" r="7" fill="#9a9a9e"/>
    <path d="M6 10h8M10 6v8" stroke="#2a2a2c" stroke-width="2"/>
  </svg>
  <svg class="screw screw--right" viewBox="0 0 20 20" aria-hidden="true">
    <circle cx="10" cy="10" r="9" fill="#3a3a3d"/><circle cx="10" cy="10" r="7" fill="#9a9a9e"/>
    <path d="M6 10h8M10 6v8" stroke="#2a2a2c" stroke-width="2"/>
  </svg>

  <div class="person">
    <p class="person__name">Dara Kell</p>
    <p class="person__role">Director</p>
  </div>

  <ul class="contacts">
    <li>
      <svg viewBox="0 0 24 24" aria-hidden="true"><path d="M6.6 10.8a15 15 0 0 0 6.6 6.6l2.2-2.2a1 1 0 0 1 1-.25 11.4 11.4 0 0 0 3.6.57 1 1 0 0 1 1 1V20a1 1 0 0 1-1 1A17 17 0 0 1 3 4a1 1 0 0 1 1-1h3.5a1 1 0 0 1 1 1c0 1.25.2 2.45.57 3.6a1 1 0 0 1-.25 1z"/></svg>
      +330-5512-0846
    </li>
    <li>
      <svg viewBox="0 0 24 24" aria-hidden="true"><path d="M2 5h20v14H2zm2 2v.5l8 5 8-5V7zm0 2.8V17h16V9.8l-8 5z"/></svg>
      infodara@kellmail.com
    </li>
    <li>
      <svg viewBox="0 0 24 24" aria-hidden="true"><path d="M12 2a10 10 0 1 0 0 20 10 10 0 0 0 0-20zm6.9 6h-3a15 15 0 0 0-1.3-3.8A8 8 0 0 1 18.9 8zM12 4c.8 1.1 1.5 2.5 1.9 4h-3.8c.4-1.5 1.1-2.9 1.9-4zM4.3 14a8 8 0 0 1 0-4h3.4a16 16 0 0 0 0 4zm.8 2h3a15 15 0 0 0 1.3 3.8A8 8 0 0 1 5.1 16zm3-8h-3a8 8 0 0 1 4.3-3.8A15 15 0 0 0 8.1 8zM12 20c-.8-1.1-1.5-2.5-1.9-4h3.8c-.4 1.5-1.1 2.9-1.9 4zm2.3-6H9.7a14 14 0 0 1 0-4h4.6a14 14 0 0 1 0 4zm.3 5.8a15 15 0 0 0 1.3-3.8h3a8 8 0 0 1-4.3 3.8zm1.7-5.8a16 16 0 0 0 0-4h3.4a8 8 0 0 1 0 4z"/></svg>
      www.larkfieldyard.com
    </li>
  </ul>
</section>

</body>
</html>
```